Podiatry (services) Business Card

I need a business design for a New Podiatry Service.
the Podiatry services will include all aspects of podiatry including;
general podiatry for all ages
corns and callus treatment
Ingrown toenails & nail surgery
Forefoot, arch and heel pain
Gait analysis
Sports Podiatry and Orthotics
Paediatric Assessments
Diabetes Foot Assessment

I would like the back of the card to have space for next appointment day and time.

I would like a nice design that is simple yet catchy. I don't like cluttered business cards. I like things to be simple yet stand out because of the finer details.

I like the colours blue and white but I'm open to other designs that have different colours.

Business

Bluewren Podiatry (Business name)

Marisol Tenbury - Podiatrist
M.Pod.P., B.Hlth. Sci, MFLsoc

Address: 58 Coleby St, Marrowdale North Vic, 3164
Phone: (03) 9416 2738
Fax: (03) 9523 4178

```html
<!DOCTYPE html>
<html lang="en">
<head>
<meta charset="utf-8">
<title>Bluewren Podiatry – Business Card</title>
<link rel="stylesheet" href="https://fonts.googleapis.com/css2?family=Source+Sans+3:wght@400;600;700&display=swap">
<style>
  :root {
    --stage: #8e8e8e;
    --card-black: #0b0b0b;
    --card-charcoal: #1d1d1d;
    --brand-blue: #1a7fd0;
    --white: #ffffff;
    --rule: #3a3a3a;
  }
  * { box-sizing: border-box; margin: 0; padding: 0; }
  html, body {
    width: 1200px; height: 900px; overflow: hidden;
    background: var(--stage);
    font-family: "Source Sans 3", "Segoe UI", Arial, sans-serif;
  }
  .stage {
    width: 1200px; height: 900px;
    display: flex; flex-direction: column; align-items: center; justify-content: center;
    gap: 40px;
  }
  .card {
    position: relative;
    width: 640px; height: 366px;
    background: radial-gradient(ellipse at 45% 40%, var(--card-charcoal), var(--card-black) 75%);
    overflow: hidden;
    color: var(--white);
    box-shadow: 0 6px 18px rgba(0,0,0,.25);
  }

  /* Front */
  .brand {
    position: absolute; left: 250px; top: 78px;
    display: flex; align-items: center; gap: 14px;
  }
  .brand-dot {
    width: 46px; height: 46px; border-radius: 50%;
    background: var(--brand-blue);
  }
  .brand-name {
    font-size: 36px; font-weight: 600; letter-spacing: 1px;
    color: var(--brand-blue); line-height: 1;
  }
  .practitioner { position: absolute; left: 44px; top: 176px; }
  .practitioner-name { font-size: 21px; font-weight: 700; color: var(--brand-blue); }
  .practitioner-role { font-weight: 400; color: var(--white); font-size: 17px; }
  .credentials { font-size: 16px; margin-top: 2px; }
  .divider {
    position: absolute; left: 300px; right: 40px; top: 240px;
    height: 1px; background: var(--rule);
  }
  .contact {
    position: absolute; right: 40px; top: 258px;
    text-align: right; font-size: 18px; line-height: 26px;
  }
  .contact-line { display: flex; justify-content: flex-end; align-items: center; gap: 8px; }
  .contact-line svg { width: 13px; height: 13px; fill: var(--brand-blue); }
  .address { margin-top: 8px; }

  /* Back */
  .services {
    position: absolute; left: 36px; top: 24px;
    list-style: none; font-size: 15.5px; font-weight: 600; line-height: 20px;
  }
  .services li { display: flex; align-items: center; gap: 9px; }
  .services li::before {
    content: ""; width: 7px; height: 7px; border-radius: 50%;
    background: var(--brand-blue); flex: none;
  }
  .back-brand {
    position: absolute; right: 34px; top: 96px;
    display: flex; align-items: center; gap: 10px;
  }
  .back-brand .brand-dot { width: 34px; height: 34px; }
  .back-brand .brand-name { font-size: 22px; }
  .appointment-band { position: absolute; inset: 0; width: 640px; height: 366px; }
  .appointment {
    position: absolute; left: 0; top: 0; width: 640px; height: 366px;
    color: var(--brand-blue); font-size: 15px; font-weight: 600;
  }
  .appointment-title {
    position: absolute; left: 250px; top: 236px;
    font-size: 18px; font-weight: 700;
  }
  .field { position: absolute; display: flex; align-items: baseline; gap: 4px; }
  .field-line { display: inline-block; border-bottom: 2px dotted var(--brand-blue); height: 1px; }
  .field-name { left: 30px; top: 262px; }
  .field-name .field-line { width: 200px; }
  .field-date { left: 236px; top: 292px; }
  .field-date .field-line { width: 150px; }
  .field-time { left: 410px; top: 318px; }
  .field-time .field-line { width: 170px; }
</style>
</head>
<body>
<main class="stage">

  <section class="card card-back" aria-label="Card back">
    <ul class="services">
      <li>General podiatry for all ages</li>
      <li>Corns and callus treatment</li>
      <li>Ingrown toenails &amp; nail surgery</li>
      <li>Forefoot, arch and heel pain</li>
      <li>Gait analysis</li>
      <li>Sports Podiatry and Orthotics</li>
      <li>Paediatric Assessments</li>
      <li>Diabetes Foot Assessment</li>
    </ul>
    <div class="back-brand">
      <span class="brand-dot"></span>
      <span class="brand-name">Bluewren Podiatry</span>
    </div>
    <svg class="appointment-band" viewBox="0 0 640 366" aria-hidden="true">
      <path d="M0 222 Q 300 180 640 300 L640 366 L0 366 Z" fill="#ffffff"/>
    </svg>
    <div class="appointment">
      <div class="appointment-title">Appointment</div>
      <div class="field field-name">Name: <span class="field-line"></span></div>
      <div class="field field-date">Date: <span class="field-line"></span></div>
      <div class="field field-time">Time: <span class="field-line"></span></div>
    </div>
  </section>

  <section class="card card-front" aria-label="Card front">
    <div class="brand">
      <span class="brand-dot"></span>
      <span class="brand-name">Bluewren Podiatry</span>
    </div>
    <div class="practitioner">
      <div class="practitioner-name">Marisol Tenbury <span class="practitioner-role">- Podiatrist</span></div>
      <div class="credentials">M.Pod.P., B.Hlth. Sci, MFLsoc</div>
    </div>
    <div class="divider"></div>
    <div class="contact">
      <div class="contact-line">(03) 9416 2738
        <svg viewBox="0 0 24 24" aria-label="Phone"><path d="M6.6 10.8a15 15 0 0 0 6.6 6.6l2.2-2.2c.3-.3.7-.4 1-.2 1.1.4 2.3.6 3.6.6.6 0 1 .4 1 1V20c0 .6-.4 1-1 1A17 17 0 0 1 3 4c0-.6.4-1 1-1h3.5c.6 0 1 .4 1 1 0 1.3.2 2.5.6 3.6.1.3 0 .7-.2 1z"/></svg>
      </div>
      <div class="contact-line">(03) 9523 4178
        <svg viewBox="0 0 24 24" aria-label="Fax"><path d="M6 2h9l3 3v4H6zM3 10h18v11H3zm4 3v2h4v-2zm0 4v2h4v-2zm7-4v2h3v-2zm0 4v2h3v-2z"/></svg>
      </div>
      <div class="address">58 Coleby St, Marrowdale North Vic, 3164</div>
    </div>
  </section>

</main>
</body>
</html>
```